Business Card Design for Marketing Firm

Looking for business card design for higher end marketing firm. Clean but impressionable/trendy. We are a marketing firm that represents manufacturers in the foodservice equipment and supply industry. Our customers are end users such has hotels, restaurants, country clubs, convention centers and casinos as well as distributors of restaurants supplies and equipment, and manufacturers of foodservice equipment and supplies.
Target Market(s)
Hotels, Restaurants, Supply & Equipment Distributors, Foodservice Manufacturers
Industry/Entity Type
Foodservice/Hospitality
Contact Information for Business Card
Name, Title, Contact Number, Email, Website, Social Media, Address
Requirements
Must have
- Clean & Simple but Serious and Impressionable

```html
<!DOCTYPE html>
<html lang="en">
<head>
<meta charset="utf-8">
<title>Meridian Service Partners – Business Card</title>
<link href="https://fonts.googleapis.com/css2?family=Open+Sans:wght@400;700&display=swap" rel="stylesheet">
<style>
  :root {
    --navy: #2b2a78;
    --ink: #1f1f2e;
    --paper: #ffffff;
    --backdrop: #d9d9d6;
  }
  html, body {
    margin: 0;
    padding: 0;
    width: 1200px;
    height: 801px;
    overflow: hidden;
    background: var(--backdrop);
    font-family: "Open Sans", Arial, sans-serif;
  }
  .stage {
    position: relative;
    width: 1200px;
    height: 801px;
  }
  .card {
    position: absolute;
    top: 246px;
    width: 540px;
    height: 309px;
    background: var(--paper);
    overflow: hidden;
    box-shadow: 0 10px 24px rgba(0,0,0,0.18);
  }
  .card--contact { left: 40px; }
  .card--brand { left: 620px; }

  .card__shapes {
    position: absolute;
    inset: 0;
  }
  .wordmark {
    color: var(--navy);
    font-weight: 700;
    text-transform: uppercase;
    letter-spacing: 0.06em;
    line-height: 1.15;
    margin: 0;
  }
  .card--contact .wordmark {
    position: absolute;
    left: 70px;
    top: 118px;
    width: 200px;
    font-size: 19px;
    text-align: center;
  }
  .divider {
    position: absolute;
    left: 280px;
    top: 70px;
    width: 1.5px;
    height: 170px;
    background: var(--navy);
  }
  .contact {
    position: absolute;
    left: 298px;
    top: 72px;
    width: 190px;
    color: var(--ink);
  }
  .contact__name {
    margin: 0;
    font-size: 17px;
    font-weight: 700;
    color: var(--navy);
    letter-spacing: 0.02em;
  }
  .contact__title {
    margin: 0 0 10px;
    font-size: 11.5px;
  }
  .contact__list {
    list-style: none;
    margin: 0 0 12px;
    padding: 0;
    font-size: 11.5px;
  }
  .contact__list li {
    display: flex;
    align-items: center;
    gap: 6px;
    margin-bottom: 3px;
  }
  .contact__list svg { width: 11px; height: 11px; flex: none; }
  .contact__address {
    margin: 0;
    font-size: 11.5px;
    line-height: 1.4;
    font-style: normal;
  }

  .card--brand .wordmark {
    position: absolute;
    left: 0;
    right: 0;
    top: 100px;
    font-size: 30px;
    text-align: center;
  }
  .social {
    position: absolute;
    left: 0;
    right: 0;
    top: 210px;
    display: flex;
    justify-content: center;
    gap: 6px;
  }
  .social__dot {
    width: 16px;
    height: 16px;
    border-radius: 50%;
    background: var(--navy);
  }
</style>
</head>
<body>
<main class="stage">

  <section class="card card--contact">
    <svg class="card__shapes" viewBox="0 0 540 309" width="540" height="309" aria-hidden="true">
      <rect width="540" height="309" fill="var(--navy)"/>
      <ellipse cx="270" cy="154" rx="250" ry="300" fill="var(--paper)"/>
      <polygon points="0,0 120,0 0,120" fill="var(--paper)"/>
      <polygon points="540,309 420,309 540,190" fill="var(--paper)"/>
    </svg>

    <p class="wordmark">Meridian Service Partners</p>
    <div class="divider"></div>

    <div class="contact">
      <p class="contact__name">DANIEL HART</p>
      <p class="contact__title">Managing Director</p>
      <ul class="contact__list">
        <li>
          <svg viewBox="0 0 12 12"><circle cx="6" cy="6" r="6" fill="var(--navy)"/><path d="M4 3.2l1 1.4-.6.7a4 4 0 0 0 2.3 2.3l.7-.6 1.4 1-.7 1.1C5.8 9 3 6.2 2.9 3.9z" fill="#fff"/></svg>
          555 010 2040
        </li>
        <li>
          <svg viewBox="0 0 12 12"><circle cx="6" cy="6" r="6" fill="var(--navy)"/><rect x="3" y="4" width="6" height="4.2" fill="none" stroke="#fff" stroke-width="0.9"/><path d="M3 4l3 2.3L9 4" fill="none" stroke="#fff" stroke-width="0.9"/></svg>
          info@meridianreps.com
        </li>
        <li>
          <svg viewBox="0 0 12 12"><circle cx="6" cy="6" r="6" fill="var(--navy)"/><circle cx="6" cy="6" r="3.2" fill="none" stroke="#fff" stroke-width="0.8"/><path d="M2.8 6h6.4M6 2.8v6.4" stroke="#fff" stroke-width="0.8"/></svg>
          www.meridianreps.com
        </li>
      </ul>
      <address class="contact__address">Your address, City<br>State, Zip 1234</address>
    </div>
  </section>

  <section class="card card--brand">
    <p class="wordmark">Meridian Service<br>Partners</p>
    <div class="social" aria-label="Social media links">
      <span class="social__dot"></span>
      <span class="social__dot"></span>
      <span class="social__dot"></span>
      <span class="social__dot"></span>
      <span class="social__dot"></span>
      <span class="social__dot"></span>
    </div>
  </section>

</main>
</body>
</html>
```